Scrum Master & Agile IT Coach Needing Business Website

Hello, my name is Joel Brandt
I am a project manger, scrum master, & agile coach. I work with IT development teams on major projects for Summit 300 companies . My project management business has a website and can be found here: www.tk-steadfast.example

I have launched a new company, ALL focused on IT Agile Coaching, I am looking to have a website created for my new company - the name of the new company is: Q's and V's - Agile IT Coaching and Training.
I have a logo and it is provided in the materials. I like to logo; I am open to different color pallets.

The website will have a total of 7 pages; I have content for 5 of the 7 pages prepared; the other 2 pages will say under construction.

Page 1 Who am I, What I do, My Experience
Demonstrated experience and progression from Scrum Master to
Program Manager to Coach

Page 2 Q's & V's - Agile Team Coaching
teams working major IT projects, multiple months/years

Page 3 Coaching @ the Team Level

Page 4 Coaching @ the Program Level ; LIMBr ART level

Pages 5 -6 Under Construction

Page 7 Presentations, Slide Decks, Reference Materials

Mentors Nook need to have this highlighted somewhere Monthly Blog
Updates

Industry/Entity Type

IT development

Coding

Coded - Design and coding required

Number of Pages Required

5+ page

Requirements
Must have
• the website must be bold - I want those who visit to remember coming to my coaching site
Nice to have
• nice to have will be a modern / futuristic website; I work with IT developers, I want a website they will like
Should not have
• should not be stiff - it should be professional but fun

```html
<!DOCTYPE html>
<html lang="en">
<head>
<meta charset="utf-8">
<title>Q's & V's - Agile IT Coaching and Training</title>
<link href="https://fonts.googleapis.com/css2?family=Orbitron:wght@600;700&family=Roboto:wght@400;500;700&display=swap" rel="stylesheet">
<style>
:root{
  --blue:#1e62a8;
  --blue-bright:#2a78c8;
  --ink:#111418;
  --body:#3a3f47;
  --pale:#f2f7fc;
  --navy:#0d2a4d;
  --white:#ffffff;
  --gold:#f0a92a;
}
*{box-sizing:border-box;margin:0;padding:0}
html,body{width:1200px;height:3401px;overflow:hidden}
body{position:relative;font-family:'Roboto',sans-serif;color:var(--ink);background:var(--white)}
.abs{position:absolute}
.display{font-family:'Orbitron',sans-serif;font-weight:700;letter-spacing:1px}
.accent{color:var(--blue)}
.btn{position:absolute;display:flex;align-items:center;justify-content:center;gap:8px;background:var(--blue);color:var(--white);border-radius:22px;font-weight:700;font-size:15px}
.btn svg{width:15px;height:15px}

/* header */
.topline{top:0;left:0;width:1200px;height:5px;background:var(--blue)}
.header{top:5px;left:0;width:1200px;height:75px;background:var(--white)}
.brand{position:absolute;display:flex;align-items:center;gap:10px;font-family:'Roboto',sans-serif;font-weight:700;font-size:26px;color:var(--blue)}
.brand .mark{width:22px;height:22px;border-radius:50%;background:var(--blue)}
.nav{top:30px;left:403px;display:flex;gap:34px;font-size:15px;color:#333}
.login{top:21px;left:957px;width:131px;height:39px}

/* hero */
.hero{top:80px;left:0;width:1200px;height:656px;background:linear-gradient(100deg,#2b2420 0%,#5a4a3d 45%,#8a7663 70%,#c7b8a6 100%)}
.hero-title{top:285px;left:106px;font-size:72px;color:var(--white)}
.hero-sub{top:378px;left:106px;font-size:40px;line-height:46px;color:var(--white)}
.get-started{top:497px;left:106px;width:166px;height:40px}

/* who i am */
.who{top:736px;left:0;width:1200px;height:528px;background:var(--pale)}
.who-photo{top:809px;left:110px;width:396px;height:396px;border-radius:50%;background:linear-gradient(135deg,#c9d6e2,#8fa4b8 60%,#5d6f82);border-bottom:6px solid var(--blue);border-left:4px solid var(--blue)}
.who h2{top:812px;left:577px;font-size:30px}
.who-name{top:858px;left:577px;font-size:20px;font-weight:500;color:var(--blue)}
.who-role{top:895px;left:577px;font-size:16px;font-weight:500}
.who-text{top:926px;left:577px;width:512px;font-size:15px;line-height:25.7px;color:var(--body);text-align:justify}
.learn{top:1149px;left:577px;width:165px;height:40px}

/* designations */
.desig h2{top:1346px;left:0;width:1200px;text-align:center;font-size:30px}
.badges{top:1425px;left:0;width:1200px;height:175px}
.profile-btn{top:1618px;width:244px;height:40px;font-size:16px;font-weight:500}

/* roles */
.roles{top:1746px;left:0;width:1200px;height:601px;background:linear-gradient(90deg,#1d5ea3 0%,#2468ae 45%,#9fb3c9 75%,#dfe3e8 100%)}
.roles-card{top:1824px;left:77px;width:533px;height:446px;background:var(--white);border-radius:20px}
.roles-card h2{position:absolute;top:90px;left:37px;font-size:29px}
.roles-list{position:absolute;top:156px;left:37px;list-style:none;font-size:22px;line-height:32px;color:#2a2d33}
.roles-list li{margin-bottom:16px}
.roles-face{top:1966px;left:518px;width:164px;height:164px;border-radius:50%;background:linear-gradient(135deg,#7c8c98,#4c5b66);border:3px solid var(--blue)}

/* experience */
.exp h2{top:2431px;left:0;width:1200px;text-align:center;font-size:30px}
.tab{position:absolute;top:2512px;width:305px;height:41px;border-radius:22px;display:flex;align-items:center;justify-content:center;font-size:15px;font-weight:500;background:var(--white);box-shadow:0 2px 10px rgba(0,0,0,.08)}
.tab.active{background:var(--blue);color:var(--white);font-size:14px}
.exp-photo{top:2603px;left:157px;width:409px;height:339px;background:linear-gradient(135deg,#e6e1da,#b9a896 55%,#4a5a70);border:2px solid #eee}
.exp-list{top:2648px;left:620px;width:460px;list-style:none;font-size:15px;line-height:21px;color:var(--body)}
.exp-list li{position:relative;padding-left:27px;margin-bottom:17px}
.exp-list li svg{position:absolute;left:0;top:4px;width:14px;height:14px}

/* footer */
.footer{top:3044px;left:0;width:1200px;height:306px;background:var(--navy);color:var(--white)}
.foot-col{position:absolute;font-size:15px}
.foot-col h3{font-size:18px;font-weight:500;margin-bottom:16px}
.foot-col li{list-style:none;display:flex;gap:14px;align-items:flex-start;margin-bottom:18px;line-height:22px}
.foot-col svg{width:12px;height:12px;margin-top:5px;flex:none}
.copyright{top:3350px;left:0;width:1200px;height:51px;background:var(--blue);color:var(--white);font-size:14px;display:flex;align-items:center;justify-content:center}
</style>
</head>
<body>

<div class="abs topline"></div>
<header class="abs header">
  <div class="brand" style="top:18px;left:110px"><span class="mark"></span>Q's &amp; V's</div>
  <nav class="abs nav"><span>WHO I AM</span><span>WHAT I DO</span><span>WHAT IS MY EXPERIENCE</span><span>CONTACT US</span></nav>
  <div class="btn login">LOGIN
    <svg viewBox="0 0 16 16"><rect x="3" y="7" width="10" height="8" rx="1" fill="#fff"/><path d="M5 7V5a3 3 0 0 1 6 0v2" stroke="#fff" stroke-width="2" fill="none"/></svg>
  </div>
</header>

<section class="abs hero" role="img" aria-label="Photo of a smiling coach working at a laptop in a bright office"></section>
<h1 class="abs display hero-title">Q'S &amp; V'S</h1>
<p class="abs display hero-sub">AGILE IT COACHING<br>AND TRAINING</p>
<div class="btn get-started">GET STARTED
  <svg viewBox="0 0 16 16"><circle cx="8" cy="8" r="7" fill="#fff"/><path d="M6 4l4 4-4 4" stroke="#1e62a8" stroke-width="2" fill="none"/></svg>
</div>

<section class="abs who"></section>
<div class="abs who-photo" role="img" aria-label="Photo of colleagues working together at a laptop"></div>
<div class="who">
  <h2 class="abs display">WHO <span class="accent">I AM</span></h2>
  <p class="abs who-name">JOEL BRANDT</p>
  <p class="abs who-role">Senior Scrum Master &amp; Team Agile Coach</p>
  <p class="abs who-text">Lorem ipsum dolor sit amet, consectetur adipiscing elit, sed do eiusmod tempor incididunt ut labore et dolore magna aliqua. Ut enim ad minim veniam, quis nostrud exercitation ullamco laboris nisi ut aliquip ex ea commodo consequat. Duis aute irure dolor in reprehenderit in voluptate velit esse cillum dolore eu fugiat nulla pariatur. Excepteur sint occaecat cupidatat non proident, sunt in culpa qui officia deserunt mollit anim id est laborum.Lorem ipsum dolor sit amet, consectetur adipiscing elit, sed do eiusmod tempor incididunt ut labore et dolore magna enim</p>
  <div class="btn learn">LEARN MORE
    <svg viewBox="0 0 16 16"><circle cx="8" cy="8" r="7" fill="#fff"/><path d="M6 4l4 4-4 4" stroke="#1e62a8" stroke-width="2" fill="none"/></svg>
  </div>
</div>

<section class="desig">
  <h2 class="abs display">COACHING <span class="accent">DESIGNATIONS</span></h2>
  <svg class="abs badges" viewBox="0 0 1200 175" aria-label="Certification badges">
    <polygon points="185,18 243,52 243,118 185,152 127,118 127,52" fill="#fff" stroke="#1a3a5c" stroke-width="6"/>
    <circle cx="357" cy="70" r="56" fill="var(--gold)"/>
    <circle cx="551" cy="75" r="66" fill="#2aa3e0"/>
    <polygon points="748,14 826,86 748,158 670,86" fill="#1a3a5c"/>
    <circle cx="993" cy="85" r="80" fill="var(--gold)"/>
  </svg>
  <div class="btn profile-btn" style="left:200px">Guild of Scrum Profile</div>
  <div class="btn profile-btn" style="left:478px">Badgefold Profile</div>
  <div class="btn profile-btn" style="left:757px">LIMBr Alliance Profile</div>
</section>

<section class="abs roles" role="img" aria-label="Photo of hands typing on a laptop beside a phone and notebook"></section>
<div class="abs roles-card">
  <h2 class="display">ROLES I HAVE HELD</h2>
  <ul class="roles-list">
    <li>Sr. Scrum Master</li>
    <li>Advanced LIMBr Scrum Master</li>
    <li>Hybrid Scrum Master/ Project Manager</li>
    <li>Business (FinanceTransformation<br>Program Manager</li>
  </ul>
</div>
<div class="abs roles-face" role="img" aria-label="Portrait photo of the coach"></div>

<section class="exp">
  <h2 class="abs display">WHAT IS MY <span class="accent">EXPERIENCE</span></h2>
  <div class="tab" style="left:116px">LIMBr Adv Scrum Master</div>
  <div class="tab" style="left:448px">Hybrid Scrum Master / Project Manger</div>
  <div class="tab active" style="left:779px">Business Transformation Program Manager</div>
  <div class="abs exp-photo" role="img" aria-label="Photo of a consultant reviewing documents with a couple"></div>
  <ul class="abs exp-list">
    <li><svg viewBox="0 0 14 14"><circle cx="7" cy="7" r="7" fill="#1e62a8"/><path d="M4 7l2 2 4-4" stroke="#fff" stroke-width="1.8" fill="none"/></svg>Business Transformation Program Manager</li>
    <li><svg viewBox="0 0 14 14"><circle cx="7" cy="7" r="7" fill="#1e62a8"/><path d="M4 7l2 2 4-4" stroke="#fff" stroke-width="1.8" fill="none"/></svg>lead business transformation efforts at the program level</li>
    <li><svg viewBox="0 0 14 14"><circle cx="7" cy="7" r="7" fill="#1e62a8"/><path d="M4 7l2 2 4-4" stroke="#fff" stroke-width="1.8" fill="none"/></svg>work with multiple product owners, business analsyts, and business stakeholders on requirements</li>
    <li><svg viewBox="0 0 14 14"><circle cx="7" cy="7" r="7" fill="#1e62a8"/><path d="M4 7l2 2 4-4" stroke="#fff" stroke-width="1.8" fill="none"/></svg>lead the international rollout, onboarding, and support of new transformational CRM tool, Nimbus CRM</li>
    <li><svg viewBox="0 0 14 14"><circle cx="7" cy="7" r="7" fill="#1e62a8"/><path d="M4 7l2 2 4-4" stroke="#fff" stroke-width="1.8" fill="none"/></svg>standup and lead multifuntional teams consisting of business and technology team members</li>
    <li><svg viewBox="0 0 14 14"><circle cx="7" cy="7" r="7" fill="#1e62a8"/><path d="M4 7l2 2 4-4" stroke="#fff" stroke-width="1.8" fill="none"/></svg>organization and communications lead</li>
  </ul>
</section>

<footer class="abs footer">
  <div class="brand" style="top:156px;left:110px;color:var(--white);font-size:30px"><span class="mark" style="background:var(--white)"></span>Q's &amp; V's</div>
  <div class="foot-col" style="top:72px;left:430px">
    <h3>Quick Links</h3>
    <ul>
      <li><svg viewBox="0 0 12 12"><path d="M1 2l4 4-4 4M6 2l4 4-4 4" stroke="#fff" stroke-width="1.6" fill="none"/></svg>Who I am</li>
      <li><svg viewBox="0 0 12 12"><path d="M1 2l4 4-4 4M6 2l4 4-4 4" stroke="#fff" stroke-width="1.6" fill="none"/></svg>What I do</li>
      <li><svg viewBox="0 0 12 12"><path d="M1 2l4 4-4 4M6 2l4 4-4 4" stroke="#fff" stroke-width="1.6" fill="none"/></svg>What is my experience</li>
      <li><svg viewBox="0 0 12 12"><path d="M1 2l4 4-4 4M6 2l4 4-4 4" stroke="#fff" stroke-width="1.6" fill="none"/></svg>Contact us</li>
    </ul>
  </div>
  <div class="foot-col" style="top:72px;left:683px">
    <h3>Other links</h3>
    <ul style="margin-top:24px">
      <li><svg viewBox="0 0 12 12"><path d="M1 2l4 4-4 4M6 2l4 4-4 4" stroke="#fff" stroke-width="1.6" fill="none"/></svg>Terms of Use</li>
      <li><svg viewBox="0 0 12 12"><path d="M1 2l4 4-4 4M6 2l4 4-4 4" stroke="#fff" stroke-width="1.6" fill="none"/></svg>Site Map</li>
      <li><svg viewBox="0 0 12 12"><path d="M1 2l4 4-4 4M6 2l4 4-4 4" stroke="#fff" stroke-width="1.6" fill="none"/></svg>Privacy Policy</li>
      <li><svg viewBox="0 0 12 12"><path d="M1 2l4 4-4 4M6 2l4 4-4 4" stroke="#fff" stroke-width="1.6" fill="none"/></svg>Disclaimer</li>
    </ul>
  </div>
  <div class="foot-col" style="top:72px;left:892px">
    <h3>Contact us</h3>
    <ul style="margin-top:26px">
      <li><svg viewBox="0 0 12 12"><path d="M6 11C3 7 2 5.5 2 4.5a4 4 0 0 1 8 0C10 5.5 9 7 6 11z" fill="#fff"/><circle cx="6" cy="4.5" r="1.5" fill="#0d2a4d"/></svg>Lorem ipsum dolor sit<br>sectetur adipiscing.</li>
      <li><svg viewBox="0 0 12 12"><rect x="3" y="1" width="6" height="10" rx="1" stroke="#fff" stroke-width="1.4" fill="none"/></svg>+1 555 010 0147</li>
      <li style="margin-top:30px"><svg viewBox="0 0 12 12"><rect x="1" y="2.5" width="10" height="7" stroke="#fff" stroke-width="1.2" fill="none"/><path d="M1 3l5 4 5-4" stroke="#fff" stroke-width="1.2" fill="none"/></svg>info@sprintwell.example</li>
    </ul>
  </div>
</footer>
<div class="abs copyright">© 2022&nbsp; Sprintwell &nbsp;|&nbsp; All Rights Reserved.</div>

</body>
</html>
```